Professional & attention grabbing.

A business card design, front and back. I already have a logo I will attach, but I am open to something new as well.
Things to include:
Name:
Title:
Phone:
Email:
Wanting something that is professional but attention grabbing.
Also we do a lot of work using drones on natural gas pipelines (leading the future)if you want to include any of that. I'm open to ideas.
Target Market(s)
Natural gas transmission industry / greenhouse gas mitigation industry
Industry/Entity Type
Business
Colors
Designer to choose colors to be used in the design.
Look and feel
Each slider illustrates characteristics of the customer's brand and the style your logo design should communicate.

```html
<!DOCTYPE html>
<html lang="en">
<head>
<meta charset="utf-8">
<title>KV Field Inspections – Business Card</title>
<link href="https://fonts.googleapis.com/css2?family=Dosis:wght@400;500;600;700&display=swap" rel="stylesheet">
<style>
  :root {
    --page-bg: #d9d5cf;
    --card-light: #eeece8;
    --card-red: #9c1c22;
    --card-red-deep: #6f0f15;
    --swoosh: #1c1c1c;
    --ink: #222222;
    --ink-on-red: #f4ecec;
  }
  html, body {
    margin: 0;
    width: 1200px;
    height: 969px;
    overflow: hidden;
    background: var(--page-bg);
    font-family: "Dosis", sans-serif;
  }
  .card {
    position: absolute;
    left: 80px;
    top: 188px;
    width: 1040px;
    height: 592px;
    border-radius: 28px;
    overflow: hidden;
    background: var(--card-light);
    box-shadow: 0 18px 40px rgba(0,0,0,0.18);
  }
  .card-shapes {
    position: absolute;
    inset: 0;
  }
  .brand {
    position: absolute;
    left: 72px;
    top: 96px;
    display: flex;
    align-items: center;
    gap: 22px;
  }
  .brand-square {
    width: 70px;
    height: 70px;
    background: var(--card-red);
  }
  .brand-name {
    font-weight: 700;
    font-size: 40px;
    line-height: 1.05;
    color: var(--ink);
    letter-spacing: 1px;
    text-transform: uppercase;
  }
  .contact {
    position: absolute;
    right: 58px;
    top: 300px;
    text-align: right;
    color: var(--ink-on-red);
  }
  .person-name {
    font-weight: 600;
    font-size: 38px;
    letter-spacing: 2px;
    margin: 0;
  }
  .person-title {
    font-weight: 400;
    font-size: 29px;
    margin: 4px 0 40px;
  }
  .contact-line {
    display: flex;
    justify-content: flex-end;
    align-items: center;
    gap: 16px;
    font-size: 28px;
    font-weight: 400;
    height: 41px;
  }
  .contact-icon {
    width: 22px;
    height: 22px;
    fill: var(--ink-on-red);
  }
</style>
</head>
<body>
  <div class="card">
    <svg class="card-shapes" viewBox="0 0 1040 592" preserveAspectRatio="none">
      <defs>
        <linearGradient id="red-panel" x1="0" y1="0" x2="1" y2="1">
          <stop offset="0" stop-color="var(--card-red)"/>
          <stop offset="1" stop-color="var(--card-red-deep)"/>
        </linearGradient>
      </defs>
      <path class="swoosh" d="M628 0 C690 200 560 450 270 592 L300 592 C600 460 720 230 672 0 Z" fill="var(--swoosh)"/>
      <path class="red-panel" d="M700 0 L1040 0 L1040 592 L292 592 C610 470 740 240 700 0 Z" fill="url(#red-panel)"/>
    </svg>

    <div class="brand">
      <div class="brand-square"></div>
      <div class="brand-name">KV Field<br>Inspections</div>
    </div>

    <div class="contact">
      <p class="person-name">ALAN MERCER</p>
      <p class="person-title">CEO/Founder</p>
      <div class="contact-line">555 210 4870
        <svg class="contact-icon" viewBox="0 0 24 24"><path d="M6.6 10.8a15.1 15.1 0 0 0 6.6 6.6l2.2-2.2c.3-.3.7-.4 1-.2 1.1.4 2.3.6 3.6.6.6 0 1 .4 1 1V20c0 .6-.4 1-1 1A17 17 0 0 1 3 4c0-.6.4-1 1-1h3.5c.6 0 1 .4 1 1 0 1.3.2 2.5.6 3.6.1.3 0 .7-.2 1z"/></svg>
      </div>
      <div class="contact-line">alan@kvfield.com
        <svg class="contact-icon" viewBox="0 0 24 24"><path d="M2 5h20v14H2z M2 5l10 8 10-8" fill="none" stroke="var(--ink-on-red)" stroke-width="2"/></svg>
      </div>
      <div class="contact-line">www.kvfield.com
        <svg class="contact-icon" viewBox="0 0 24 24"><circle cx="12" cy="12" r="9" fill="none" stroke="var(--ink-on-red)" stroke-width="2"/><path d="M3 12h18M12 3c3 3 3 15 0 18M12 3c-3 3-3 15 0 18" fill="none" stroke="var(--ink-on-red)" stroke-width="1.6"/></svg>
      </div>
    </div>
  </div>
</body>
</html>
```